Website Widget/Code Snippet Website

We create a number of website plugins (called widgets) for a website builder called LumaSite. It is a library of widgets that users who design their site in LumaSite can use on their website.
I am looking for a new design for this site;
https://www.quillpatchery.net
The website is going to official launch so I would like a new, clean design that emphasizes the huge library of widgets for LumaSite.
Tag Line: QuillPatchery Makes Anything Possible
We should emphasize the Sign Up option which provides a subscription to access the widgets.
I would like;
1. A home page
2. A widgets page which shows all the available widgets
3. A pricing/signup page
4. Widget information page
One overall simplistic design that is easy to navigate
Industry/Entity Type
Website building and website design
Number of Pages Required
4 page
Look and feel

```html
<!DOCTYPE html>
<html lang="en">
<head>
<meta charset="utf-8">
<title>QuillPatchery — Widgets for LumaSite</title>
<link href="https://fonts.googleapis.com/css2?family=Montserrat:wght@400;500;600;700&family=Open+Sans:wght@400;600&display=swap" rel="stylesheet">
<style>
:root{
  --brand:#1ec8f2;
  --brand-deep:#0aa9d6;
  --ink:#1c1c22;
  --body:#4a4f57;
  --muted:#8c9096;
  --line:#e3e6ea;
  --pale:#e6f7fd;
  --grey-bg:#f1f2f4;
  --footer:#1e1e20;
  --white:#ffffff;
}
*{box-sizing:border-box;margin:0;padding:0}
html,body{width:1200px;height:4057px;overflow:hidden;background:var(--white)}
body{position:relative;font-family:"Open Sans",sans-serif;color:var(--body)}
.abs{position:absolute}
.heading{font-family:"Montserrat",sans-serif;color:var(--ink)}
.btn{position:absolute;display:flex;align-items:center;justify-content:center;background:var(--brand);color:var(--white);font-family:"Montserrat",sans-serif;font-weight:700;font-size:16px;border-radius:4px}
.logo{display:flex;align-items:center;gap:10px;font-family:"Montserrat",sans-serif;font-weight:600;font-size:25px;color:var(--brand)}
.logo-mark{width:26px;height:26px;border:3px solid var(--brand);border-radius:6px}

/* header */
.site-header{position:absolute;top:0;left:0;width:1200px;height:107px;background:var(--white)}
.site-header .logo{position:absolute;left:110px;top:36px}
.main-nav a{position:absolute;top:42px;font-size:15px;color:var(--ink);text-decoration:none}
.main-nav a.active{color:var(--brand)}

/* hero */
.hero{position:absolute;top:107px;left:0;width:1200px;height:644px;background:linear-gradient(90deg,#2cc6ee,#22cff6 60%,#2ccbf2)}
.hero-title{position:absolute;left:109px;top:165px;font-family:"Montserrat",sans-serif;font-weight:700;font-size:62px;line-height:68px;color:var(--white)}
.hero .outline-btn{position:absolute;left:112px;top:416px;width:165px;height:50px;border:2px solid var(--white);border-radius:4px;color:var(--white);font-family:"Montserrat",sans-serif;font-weight:700;font-size:16px;display:flex;align-items:center;justify-content:center}
.hero-photo{position:absolute;left:630px;top:66px;width:441px;height:578px;border-radius:30px 30px 0 0;background:linear-gradient(180deg,#36d4f7,#e3a23a 55%,#1f5a82)}
.arrow{position:absolute;width:22px;height:32px}

/* countdown */
.count-title{position:absolute;top:818px;width:1200px;text-align:center;font-family:"Montserrat",sans-serif;font-weight:500;font-size:22px;color:var(--ink)}
.count-row{position:absolute;left:110px;top:898px;width:978px;height:137px;border-top:1px solid var(--line);border-bottom:1px solid var(--line);display:flex}
.count-cell{flex:1;text-align:center;border-right:1px solid var(--line);padding-top:26px}
.count-cell:last-child{border-right:none}
.count-cell .num{font-family:"Montserrat",sans-serif;font-weight:600;font-size:32px;color:var(--ink)}
.count-cell .lbl{font-family:"Montserrat",sans-serif;font-size:22px;color:var(--ink);margin-top:6px}

/* before */
.before{position:absolute;top:1121px;left:0;width:1200px;height:471px;background:var(--pale)}
.section-title{font-family:"Montserrat",sans-serif;font-weight:600;font-size:33px;color:var(--ink)}
.search{position:absolute;left:112px;top:222px;width:395px;height:51px;background:var(--white);border:1px solid var(--line);border-radius:26px;font-size:15px;color:var(--muted);padding:16px 30px}
.search-go{position:absolute;right:4px;top:5px;width:40px;height:40px;border-radius:50%;background:var(--brand)}
.tile{position:absolute;width:104px;height:107px;background:var(--white);box-shadow:0 6px 18px rgba(0,0,0,.12);display:flex;align-items:center;justify-content:center}
.tile i{display:block;width:52px;height:40px;border-radius:10px}

/* now */
.app-ring{position:absolute;border:6px solid var(--brand);border-radius:28px;background:var(--white);display:flex;align-items:center;justify-content:center}
.app-ring i{display:block;border-radius:50%;background:#1d2134}
.body-text{font-size:17px;line-height:34px;color:var(--body)}

/* next */
.next{position:absolute;top:2074px;left:0;width:1200px;height:525px;background:linear-gradient(90deg,#3fc5ec,#1fcbf4)}
.gallery-frame{position:absolute;left:614px;top:73px;width:452px;height:389px;border:2px solid var(--white);border-radius:40px 0 0 30px}
.gallery-main{position:absolute;left:11px;top:0;width:352px;height:378px;border-radius:30px 0 0 20px;background:radial-gradient(circle at 50% 30%,#c58aa0,#3a4a78 45%,#101a2e)}
.thumbs{position:absolute;left:366px;top:0;width:85px;height:378px;background:var(--white)}
.thumb{height:79.6px;position:relative}
.thumb i{display:block;height:31px;background:linear-gradient(90deg,#2b3552,#5b6a86)}
.thumb span{display:block;font-size:11px;color:var(--ink);padding:8px 2px 0}

/* beta */
.beta-title{position:absolute;top:2671px;width:1200px;text-align:center;font-family:"Montserrat",sans-serif;font-weight:500;font-size:32px;line-height:47px;color:var(--ink)}
.beta-box{position:absolute;top:2811px;width:176px;height:158px;background:var(--white);border-radius:22px;box-shadow:0 4px 18px rgba(0,0,0,.08);text-align:center;padding-top:30px}
.beta-box .num{font-family:"Montserrat",sans-serif;font-weight:600;font-size:44px;color:var(--ink)}
.beta-box .lbl{font-family:"Montserrat",sans-serif;font-size:21px;color:var(--brand);margin-top:4px}

/* contact */
.contact{position:absolute;top:3056px;left:0;width:1200px;height:637px;background:var(--grey-bg)}
.field{position:absolute;background:var(--white);border-radius:3px;box-shadow:0 2px 6px rgba(0,0,0,.05);font-size:14px;color:var(--body);padding:22px 22px}

/* footer */
.site-footer{position:absolute;top:3693px;left:0;width:1200px;height:364px;background:var(--footer);color:var(--white)}
.foot-h{position:absolute;top:70px;font-family:"Montserrat",sans-serif;font-weight:600;font-size:19px}
.foot-list{position:absolute;top:112px;list-style:none;font-size:15px;line-height:25.7px}
.foot-list li::before{content:"»";margin-right:12px}
.social{position:absolute;top:3854px;width:38px;height:38px;border-radius:50%;background:var(--white)}
.social::after{content:"";position:absolute;inset:12px;border-radius:50%;background:var(--brand)}
</style>
</head>
<body>

<header class="site-header">
  <div class="logo"><span class="logo-mark"></span>QuillPatchery</div>
  <nav class="main-nav">
    <a class="active" style="left:409px">Home</a>
    <a style="left:488px">Widgets</a>
    <a style="left:583px">Pricing &amp; Signup</a>
    <a style="left:739px">Widget information</a>
  </nav>
  <div class="btn" style="left:924px;top:27px;width:164px;height:49px">Sign Up For Free</div>
</header>

<section class="hero">
  <h1 class="hero-title">QuillPatchery<br>Makes Anything<br>Possible</h1>
  <div class="outline-btn">Sign Up For Free</div>
  <div class="hero-photo" role="img" aria-label="Smiling woman holding an open laptop in front of large white widget frames"></div>
  <svg class="arrow" style="left:54px;top:305px" viewBox="0 0 22 32"><path d="M17 3 5 16l12 13" fill="none" stroke="#fff" stroke-width="3"/></svg>
  <svg class="arrow" style="left:1121px;top:305px" viewBox="0 0 22 32"><path d="M5 3l12 13L5 29" fill="none" stroke="#fff" stroke-width="3"/></svg>
</section>

<h2 class="count-title">We're Giving Away Our Widgets FREE For The Next</h2>
<div class="count-row">
  <div class="count-cell"><div class="num">00</div><div class="lbl">Days</div></div>
  <div class="count-cell"><div class="num">00</div><div class="lbl">Hours</div></div>
  <div class="count-cell"><div class="num">00</div><div class="lbl">Minutes</div></div>
  <div class="count-cell"><div class="num">00</div><div class="lbl">Seconds</div></div>
</div>

<section class="before">
  <h2 class="section-title abs" style="left:109px;top:68px">Before</h2>
  <p class="abs" style="left:111px;top:128px;width:470px;font-size:15px;line-height:27px;color:var(--ink)">With LumaSite you can easily create stunning websites just by dragging and dropping.</p>
  <div class="search">Website<span class="search-go"></span></div>
  <div class="btn" style="left:112px;top:314px;width:146px;height:49px;font-size:15px">Get LumaSite</div>
  <div class="tile" style="left:702px;top:98px"><i style="background:#e62117"></i></div>
  <div class="tile" style="left:702px;top:265px"><i style="background:#f2a21b"></i></div>
  <div class="tile" style="left:866px;top:185px;background:var(--brand)"><i style="background:#ffffff;width:40px"></i></div>
</section>

<section>
  <div class="app-ring" style="left:118px;top:1739px;width:109px;height:108px"><i style="width:46px;height:46px;border-radius:10px"></i></div>
  <div class="app-ring" style="left:258px;top:1682px;width:164px;height:165px;border-radius:34px"><i style="width:98px;height:98px;border-radius:22px;background:#1659e6"></i></div>
  <div class="app-ring" style="left:118px;top:1877px;width:109px;height:111px"><i style="width:54px;height:54px"></i></div>
  <div class="app-ring" style="left:258px;top:1877px;width:109px;height:111px"><i style="width:56px;height:56px;background:#14243e"></i></div>
  <svg class="abs" style="left:480px;top:1795px" width="26" height="26" viewBox="0 0 26 26"><circle cx="13" cy="13" r="13" fill="#1ec8f2"/><path d="M11 7l6 6-6 6" fill="none" stroke="#fff" stroke-width="3"/></svg>
  <svg class="abs" style="left:480px;top:1847px" width="26" height="26" viewBox="0 0 26 26"><circle cx="13" cy="13" r="13" fill="#8d9096"/><path d="M15 7l-6 6 6 6" fill="none" stroke="#fff" stroke-width="3"/></svg>
  <h2 class="section-title abs" style="left:611px;top:1674px;font-size:31px">Now</h2>
  <p class="abs body-text" style="left:613px;top:1744px;width:470px">Use our library of advanced widgets to add everything from image galleries, slide shows, e-commerce stores and so much more to your LumaSite website.</p>
  <div class="btn" style="left:613px;top:1885px;width:148px;height:51px;font-size:15px">See Widgets</div>
</section>

<section class="next">
  <h2 class="section-title abs" style="left:109px;top:134px;color:var(--white);font-size:37px">Next</h2>
  <p class="abs body-text" style="left:111px;top:207px;width:420px;color:var(--white)">We don't plan to stop there, more widgets are on their way! Let us know if there are any widgets you need!</p>
  <svg class="abs" style="left:110px;top:334px" width="50" height="20" viewBox="0 0 50 20"><path d="M8 3 2 10l6 7" fill="none" stroke="#9fe6fb" stroke-width="2.2"/><path d="M37 3l6 7-6 7" fill="none" stroke="#fff" stroke-width="2.2"/></svg>
  <div class="gallery-frame">
    <div class="gallery-main" role="img" aria-label="Photo of sunglasses on a table with blurred city lights behind"></div>
    <div class="thumbs">
      <div class="thumb"><i></i><span>Glasses</span></div>
      <div class="thumb"><i></i><span>Night</span></div>
      <div class="thumb"><i style="background:linear-gradient(90deg,#2a3358,#d7903e)"></i><span>Couple</span></div>
      <div class="thumb"><i style="background:linear-gradient(90deg,#5a6472,#c9ced6)"></i><span>Stairs</span></div>
      <div class="thumb"><i></i><span>Hands</span></div>
    </div>
  </div>
</section>

<h2 class="beta-title">Our widgets are free while in beta testing until the<br>counter runs out!</h2>
<div class="beta-box" style="left:189px"><div class="num">00</div><div class="lbl">Days</div></div>
<div class="beta-box" style="left:405px"><div class="num">00</div><div class="lbl">Hours</div></div>
<div class="beta-box" style="left:620px"><div class="num">00</div><div class="lbl">Minutes</div></div>
<div class="beta-box" style="left:835px"><div class="num">00</div><div class="lbl">Seconds</div></div>

<section class="contact">
  <h2 class="heading abs" style="top:65px;width:1200px;text-align:center;font-weight:500;font-size:32px">Have questions? Send us a message!</h2>
  <div class="field" style="left:203px;top:146px;width:384px;height:63px">First Name</div>
  <div class="field" style="left:611px;top:146px;width:384px;height:63px">Last Name</div>
  <div class="field" style="left:203px;top:234px;width:384px;height:63px">Email</div>
  <div class="field" style="left:611px;top:234px;width:384px;height:63px">Phone</div>
  <div class="field" style="left:203px;top:321px;width:792px;height:120px">Message</div>
  <div class="abs" style="left:204px;top:472px;display:flex;align-items:center;gap:8px;font-size:13px;color:var(--ink)"><span style="width:12px;height:12px;border:1px solid #aaa;background:#fff"></span>I'm not a robot</div>
  <div class="btn" style="left:539px;top:516px;width:121px;height:51px">Send</div>
</section>

<footer class="site-footer">
  <div class="logo abs" style="left:110px;top:106px;color:var(--brand)"><span class="logo-mark"></span>QuillPatchery</div>
  <div class="abs" style="left:389px;top:75px;width:1px;height:170px;background:#36363a"></div>
  <div class="foot-h" style="left:417px">Navigation</div>
  <ul class="foot-list" style="left:417px"><li>Home</li><li>Widgets</li><li>Pricing &amp; Signup</li><li>Widget information</li></ul>
  <div class="foot-h" style="left:608px">Highlighted Widgets</div>
  <ul class="foot-list" style="left:608px"><li>Fading Navigation Bar Pro</li><li>Advanced Image Wrap</li><li>E-Store Advanced</li><li>Popup On Scroll</li></ul>
  <div class="foot-h" style="left:880px">Contact us</div>
  <svg class="abs" style="left:880px;top:114px" width="13" height="18" viewBox="0 0 13 18"><path d="M6.5 0A6.5 6.5 0 0 0 0 6.5C0 11 6.5 18 6.5 18S13 11 13 6.5A6.5 6.5 0 0 0 6.5 0z" fill="#fff"/><circle cx="6.5" cy="6.5" r="2.4" fill="#1e1e20"/></svg>
  <p class="abs" style="left:904px;top:111px;font-size:15px;line-height:25px">Lorem ipsum dolor sit<br>amet, consectetur</p>
  <svg class="abs" style="left:880px;top:183px" width="15" height="15" viewBox="0 0 15 15"><path d="M3 0l3 4-2 2c1 2 3 4 5 5l2-2 4 3-2 3C6 15 0 9 0 2z" fill="#fff"/></svg>
  <p class="abs" style="left:904px;top:180px;font-size:15px">+1 (888) 888 8888</p>
  <svg class="abs" style="left:880px;top:225px" width="17" height="12" viewBox="0 0 17 12"><rect width="17" height="12" rx="1" fill="#fff"/><path d="M0 1l8.5 6L17 1" fill="none" stroke="#1e1e20" stroke-width="1.5"/></svg>
  <p class="abs" style="left:906px;top:221px;font-size:15px">info@quillpatchery.net</p>
  <div class="abs" style="left:110px;top:284px;width:978px;height:1px;background:#36363a"></div>
  <p class="abs" style="top:320px;width:1200px;text-align:center;font-size:15px">©Copyrights 2022 Quillpatchery &nbsp;|&nbsp;&nbsp; All Rights Reserved</p>
</footer>
<span class="social" style="left:110px"></span>
<span class="social" style="left:157px"></span>
<span class="social" style="left:203px"></span>
<span class="social" style="left:249px"></span>

</body>
</html>
```